Home Remodeling company needs a business card design

we need a business card design for home remodeling company in hamilton county, indiana USA. we offers a wide range of construction services including whole house renovations, Design and Build Basements and Kitchen and Bathroom Remodeling . we would like to see designs for both site of business card that use the same color of the company logo and also including all information below :
1- Karim Feltous CEO / General Contractor
2- all company contacts Telephone numbers ( 1-888-DULOM-47 ) ( 317-555-0193) email address ( info@dulomhome.com) website ( www.dulomhome.com ) and social media logos (Facebook- twitter- google plus )
3- company logo
4- licensed . insured . bonded

```html
<!DOCTYPE html>
<html lang="en">
<head>
<meta charset="utf-8">
<title>DULOM Home Remodeling – Business Card</title>
<link rel="stylesheet" href="https://fonts.googleapis.com/css2?family=Montserrat:wght@700&family=Open+Sans:wght@400;600&display=swap">
<style>
  :root {
    --backdrop: #000000;
    --card: #ffffff;
    --ink: #3a3a3c;
    --ink-soft: #6d6e70;
    --text: #1d1d1d;
    --accent: #c8242b;
  }
  * { margin: 0; padding: 0; box-sizing: border-box; }
  html, body { width: 1200px; height: 900px; overflow: hidden; background: var(--backdrop); }
  body { position: relative; font-family: "Open Sans", Arial, sans-serif; color: var(--text); }

  .card { position: absolute; top: 275px; width: 477px; height: 293px; background: var(--card); }
  .card--front { left: 116px; border-radius: 0 58px 0 58px; }
  .card--back { left: 622px; border-radius: 58px 0 58px 0; }

  .brand { position: absolute; display: flex; flex-direction: column; }
  .brand__row { display: flex; align-items: center; gap: 8px; }
  .brand__mark { width: 8px; height: 8px; background: var(--accent); }
  .brand__name { font-family: "Montserrat", Arial, sans-serif; font-weight: 700; color: var(--ink); line-height: 1; letter-spacing: 1px; }
  .brand__descriptor { color: var(--ink-soft); text-transform: uppercase; line-height: 1; }

  .card--front .brand { left: 31px; top: 34px; }
  .card--front .brand__name { font-size: 38px; }
  .card--front .brand__descriptor { font-size: 12.5px; letter-spacing: 4.6px; margin-top: 6px; }

  .social { position: absolute; right: 38px; top: 88px; display: flex; gap: 10px; }
  .social__dot { width: 21px; height: 21px; border-radius: 50%; background: var(--text); }

  .person { position: absolute; right: 35px; top: 132px; text-align: right; }
  .person__name { color: var(--accent); font-weight: 600; font-size: 16px; line-height: 20px; }
  .person__role { font-size: 12.5px; line-height: 18px; }

  .contacts { position: absolute; right: 34px; top: 191px; list-style: none; }
  .contacts__item { display: flex; justify-content: flex-end; align-items: center; gap: 9px; font-size: 13px; height: 20px; }
  .contacts__icon { width: 10px; height: 10px; fill: var(--accent); stroke: var(--accent); }

  .card--back .brand { left: 125px; top: 120px; }
  .card--back .brand__name { font-size: 38px; }
  .card--back .brand__descriptor { font-size: 12.5px; letter-spacing: 4.6px; margin-top: 6px; }
  .credentials { position: absolute; left: 0; right: 0; top: 177px; text-align: center; font-size: 15px; font-weight: 600; color: var(--text); }
  .credentials__sep { display: inline-block; width: 7px; height: 7px; border-radius: 50%; background: var(--accent); margin: 0 4px 2px; }
</style>
</head>
<body>
  <section class="card card--front">
    <div class="brand">
      <div class="brand__row"><span class="brand__name">DULOM</span><span class="brand__mark"></span></div>
      <span class="brand__descriptor">Home Remodeling</span>
    </div>
    <div class="social" aria-label="Social media">
      <span class="social__dot"></span><span class="social__dot"></span><span class="social__dot"></span>
    </div>
    <div class="person">
      <p class="person__name">Karim Feltous</p>
      <p class="person__role">CEO / General Contractor</p>
    </div>
    <ul class="contacts">
      <li class="contacts__item">1-888-DULOM-47
        <svg class="contacts__icon" viewBox="0 0 10 10"><path stroke="none" d="M2 0.5l1.6 2-1 1.2c.6 1.3 1.5 2.2 2.7 2.8l1.2-1 2 1.6-1 1.9C4.5 9 1 5.5 0.1 1.5z"/></svg></li>
      <li class="contacts__item">317-555-0193
        <svg class="contacts__icon" viewBox="0 0 10 10"><path stroke="none" d="M2 0.5l1.6 2-1 1.2c.6 1.3 1.5 2.2 2.7 2.8l1.2-1 2 1.6-1 1.9C4.5 9 1 5.5 0.1 1.5z"/></svg></li>
      <li class="contacts__item">info@dulomhome.com
        <svg class="contacts__icon" viewBox="0 0 10 10"><rect stroke="none" x="0" y="1.5" width="10" height="7"/><path fill="none" stroke="#fff" stroke-width="1" d="M0.5 2l4.5 3.5L9.5 2"/></svg></li>
      <li class="contacts__item">www.dulomhome.com
        <svg class="contacts__icon" viewBox="0 0 10 10"><g fill="none" stroke-width="1.3"><rect x="0.8" y="4.2" width="5" height="3" rx="1.5" transform="rotate(-45 3.3 5.7)"/><rect x="4.2" y="2.8" width="5" height="3" rx="1.5" transform="rotate(-45 6.7 4.3)"/></g></svg></li>
    </ul>
  </section>

  <section class="card card--back">
    <div class="brand">
      <div class="brand__row"><span class="brand__name">DULOM</span><span class="brand__mark"></span></div>
      <span class="brand__descriptor">Home Remodeling</span>
    </div>
    <p class="credentials">Licensed <span class="credentials__sep"></span> Insured <span class="credentials__sep"></span> Bonded</p>
  </section>
</body>
</html>
```